Brightfield Ventures Inc. Letterhead

Creation of attractive and eye catching letterhead for a business start-up for the construction industry. Letterhead must relate to construction, but avoid standard hammer and tools in the design.

I forgot to add some details, sorry about that. Some pertinent info: Ph: 916-555-0187 brightfieldventures.example 448 Willowmere Ave, Ste 210 Folsom, CA 95999 info@brightfieldventures.example not sure if slogan should be in there" “Connecting construction professionals to create a purpose driven industry.” must be able to be used in word. Thanks!

```html
<!DOCTYPE html>
<html lang="en">
<head>
<meta charset="utf-8">
<title>Brightfield Ventures Inc. Letterhead</title>
<link href="https://fonts.googleapis.com/css2?family=Lato:wght@400;700&family=Yellowtail&display=swap" rel="stylesheet">
<style>
  :root {
    --navy: #1b1f5c;
    --red: #c8202a;
    --text: #4a4a4a;
    --paper: #ffffff;
    --rule: #9a9a9a;
  }
  * { margin: 0; padding: 0; box-sizing: border-box; }
  html, body { width: 917px; height: 1200px; overflow: hidden; background: var(--paper); }
  .letterhead {
    position: relative;
    width: 917px;
    height: 1200px;
    background: var(--paper);
    font-family: "Lato", Arial, sans-serif;
    color: var(--text);
  }
  .brand {
    position: absolute;
    left: 76px;
    top: 80px;
    display: flex;
    align-items: center;
    gap: 10px;
  }
  .brand-mark { width: 16px; height: 16px; background: var(--red); }
  .brand-name {
    font-weight: 700;
    font-size: 22px;
    letter-spacing: 0.5px;
    color: var(--navy);
  }
  .contact {
    position: absolute;
    left: 641px;
    top: 34px;
    padding-left: 12px;
    border-left: 1px solid var(--rule);
    font-size: 13.5px;
    line-height: 20px;
    color: var(--text);
    height: 114px;
  }
  .contact-row { display: flex; align-items: flex-start; gap: 4px; white-space: nowrap; }
  .contact-row svg { width: 10px; height: 10px; margin-top: 5px; flex: none; }
  .contact-gap { height: 12px; }
  .indent { padding-left: 14px; white-space: nowrap; }
  .greeting {
    position: absolute;
    left: 78px;
    top: 236px;
    font-weight: 700;
    font-size: 17px;
    color: var(--navy);
  }
  .body-copy {
    position: absolute;
    left: 78px;
    top: 281px;
    width: 762px;
    font-size: 18px;
    line-height: 28.4px;
    text-align: justify;
    hyphens: manual;
  }
  .body-copy p + p { margin-top: 19px; }
  .closing {
    position: absolute;
    left: 80px;
    top: 782px;
    font-size: 20px;
    color: #222;
  }
  .signature {
    position: absolute;
    left: 80px;
    top: 812px;
    font-family: "Yellowtail", "Brush Script MT", cursive;
    font-size: 40px;
    line-height: 1.2;
    color: var(--navy);
  }
  .footer-bands {
    position: absolute;
    left: 0;
    bottom: 0;
    width: 917px;
    height: 10px;
    display: flex;
    gap: 7px;
  }
  .band { flex: 1; height: 100%; }
  .band-navy { background: var(--navy); }
  .band-red { background: var(--red); }
</style>
</head>
<body>
<div class="letterhead">
  <div class="brand">
    <span class="brand-mark"></span>
    <span class="brand-name">Brightfield Ventures Inc.</span>
  </div>

  <div class="contact">
    <div class="contact-row">
      <svg viewBox="0 0 10 10"><circle cx="5" cy="5" r="4.2" fill="none" stroke="#c8202a" stroke-width="1.4"/><circle cx="5" cy="4.5" r="1.5" fill="#c8202a"/></svg>
      <span>448 Willowmere Ave, Ste 210</span>
    </div>
    <div class="indent">Folsom, CA 95999</div>
    <div class="contact-gap"></div>
    <div class="contact-row">
      <svg viewBox="0 0 10 10"><path d="M2.5 1 L4 1 L4.6 3 L3.6 3.8 Q4.6 6 6.2 6.6 L7 5.6 L9 6.2 L9 7.6 Q8.5 9 7 9 Q1 8 1 2.5 Q1 1 2.5 1 Z" fill="#c8202a"/></svg>
      <span>916-555-0187</span>
    </div>
    <div class="contact-row">
      <svg viewBox="0 0 10 10"><rect x="0.5" y="2" width="9" height="6.5" rx="1" fill="#c8202a"/><path d="M0.8 2.4 L5 5.6 L9.2 2.4" fill="none" stroke="#fff" stroke-width="1"/></svg>
      <span>info@brightfieldventures.example</span>
    </div>
    <div class="contact-row">
      <svg viewBox="0 0 10 10"><circle cx="5" cy="5" r="4.3" fill="none" stroke="#c8202a" stroke-width="1.2"/><ellipse cx="5" cy="5" rx="1.8" ry="4.3" fill="none" stroke="#c8202a" stroke-width="0.9"/><line x1="0.7" y1="5" x2="9.3" y2="5" stroke="#c8202a" stroke-width="0.9"/></svg>
      <span>brightfieldventures.example</span>
    </div>
  </div>

  <div class="greeting">Dear Mr. Lorem,</div>

  <div class="body-copy">
    <p>Lorem ipsum dolor sit amet, consectetuer adipiscing elit, sed diam nonummy nibh euismod tinci&shy;dunt ut laoreet dolore magna aliquam erat volutpat. Ut wisi enim ad minim veniam, quis nostrud exerci tation ullamcorper suscipit lobortis nisl ut aliquip ex ea commodo consequat. Duis autem vel eum iriure dolor in hendiusto odio dignissim qui blandit praesent luptatum zzril delenit augue duis dolore te feugait nulla facilisi.</p>
    <p>Lorem ipsum dolor sit amet, consectetuer adipiscing elit, sed diam nonummy nibh euismod tinci&shy;dunt ut laoreet dolore magna aliquam erat volutpat. Ut wisi enim ad minim veniam, quis nostrud exerci tation ullamcorper suscipit lobortis nisl ut aliquip ex ea commodo consequat. Duis autem vel eum iriure dolor in hendiusto odio dignissim qui blandit praesent luptatum zzril delenit augue duis dolore te feugait nulla facilisi.</p>
    <p>Lorem ipsum dolor sit amet, consectetuer adipiscing elit, sed diam nonummy nibh euismod tinci&shy;dunt ut laoreet dolore magna aliquam erat volutpat. Ut wisi enim ad minim veniam, quis nostrud exerci tation ullamcorper suscipit lobortis nisl ut aliquip ex ea commodo consequat. Duis autem vel eum iriure dolor in hendiusto odio dignissim qui blandit praesent luptatum zzril delenit augue duis dolore te feugait nulla facilisi.</p>
  </div>

  <div class="closing">Sincerely Your,</div>
  <div class="signature">Your Name</div>

  <div class="footer-bands">
    <span class="band band-navy"></span>
    <span class="band band-red"></span>
    <span class="band band-navy"></span>
  </div>
</div>
</body>
</html>
```